Design for schnapps bottle label "Río Ámbar"

Hi! On a small land lot we are producing our own Italian schnapps "Grappa". For the bottles we would like to modernize our current labes that you find below. The two cats looking at each other should remain, but updated and more modern. I am very much looking forward to your suggestions. Best, Jens

Target Market(s)

Schnapps bottle label

Requirements
Must have
• Cats should resemble the cats that are decorating the house entry (see attached), however, should have a more modern appearance.

Text elements should remain: "Grappa", "Río Ámbar", "Legnoso", "[Vintage Year], "Raccolta No", "Vol %"
Should not have
• Current ornament can be used, replaced or deleted (whatever looks best)

```html
<!DOCTYPE html>
<html lang="it">
<head>
<meta charset="utf-8">
<title>Grappa Legnoso 2015 – Río Ámbar</title>
<link rel="stylesheet" href="https://fonts.googleapis.com/css2?family=Federant&family=Mrs+Saint+Delafield&family=Cormorant+Garamond:wght@600&display=swap">
<style>
  :root {
    --backdrop: #8a827e;
    --paper: #efefed;
    --ink: #262626;
    --olive-dark: #8d8f10;
    --olive: #a9ad1c;
    --olive-light: #c4c74a;
    --olive-deep: #6c6d0a;
  }
  * { margin: 0; padding: 0; box-sizing: border-box; }
  html, body {
    width: 1200px;
    height: 851px;
    overflow: hidden;
  }
  body {
    background: var(--backdrop);
    position: relative;
  }
  .label {
    position: absolute;
    left: 344px;
    top: 35px;
    width: 512px;
    height: 780px;
    background: var(--paper);
    box-shadow: 0 6px 18px rgba(0,0,0,0.25);
    overflow: hidden;
  }
  .label__top-band {
    position: absolute;
    left: 0; top: 0; width: 100%;
    height: 20px;
    background: var(--olive-dark);
  }
  .label__top-band--light {
    top: 20px;
    height: 16px;
    background: var(--olive);
  }
  .label__title {
    position: absolute;
    top: 54px;
    width: 100%;
    text-align: center;
    font-family: "Federant", serif;
    font-weight: 400;
    font-size: 108px;
    letter-spacing: -2px;
    line-height: 140px;
    height: 140px;
    color: var(--ink);
    text-shadow: 2px 2px 0 #fff, 3px 3px 0 var(--ink);
  }
  .label__style {
    position: absolute;
    top: 226px;
    width: 100%;
    height: 70px;
    text-align: center;
    line-height: 70px;
  }
  .label__cuvee {
    font-family: "Mrs Saint Delafield", cursive;
    font-size: 56px;
    color: var(--ink);
  }
  .label__year {
    font-family: "Federant", serif;
    font-size: 30px;
    color: var(--olive-dark);
  }
  .label__of {
    position: absolute;
    top: 300px;
    left: 0;
    width: 100%;
    height: 44px;
    line-height: 44px;
    text-align: center;
    font-family: "Mrs Saint Delafield", cursive;
    font-size: 40px;
    color: var(--ink);
    z-index: 2;
  }
  .label__cat {
    position: absolute;
    top: 330px;
    height: 124px;
    width: 170px;
    border-radius: 8px;
    background: linear-gradient(180deg, #3a3a3a, var(--ink));
  }
  .label__cat--left { left: 66px; }
  .label__cat--right { left: 276px; }
  .label__brand {
    position: absolute;
    top: 478px;
    width: 100%;
    height: 90px;
    text-align: center;
    font-family: "Federant", serif;
    font-size: 68px;
    letter-spacing: -1px;
    line-height: 90px;
    color: var(--olive-dark);
  }
  .label__details {
    position: absolute;
    left: 22px;
    right: 22px;
    top: 604px;
    height: 36px;
    display: flex;
    justify-content: space-between;
    align-items: baseline;
    color: var(--ink);
  }
  .label__batch, .label__abv {
    font-family: "Cormorant Garamond", serif;
    font-weight: 600;
    font-size: 22px;
    line-height: 36px;
  }
  .label__batch em, .label__abv em {
    font-family: "Mrs Saint Delafield", cursive;
    font-style: normal;
    font-size: 28px;
    font-weight: 400;
  }
  .label__rule {
    position: absolute;
    left: 0; top: 649px; width: 100%;
    height: 7px;
    background: var(--olive);
  }
  .label__ornament {
    position: absolute;
    left: 0; top: 656px; width: 100%;
    height: 124px;
    background: linear-gradient(135deg, var(--olive-light), var(--olive) 55%, var(--olive-deep));
  }
</style>
</head>
<body>
  <main class="label">
    <div class="label__top-band"></div>
    <div class="label__top-band label__top-band--light"></div>

    <h1 class="label__title">Grappa</h1>

    <p class="label__style">
      <span class="label__cuvee">“legnoso”</span><span class="label__year">2015</span>
    </p>

    <div class="label__cat label__cat--left" role="img" aria-label="Black cat silhouette crouching to the right, tail curled into a spiral"></div>
    <div class="label__cat label__cat--right" role="img" aria-label="Black cat silhouette crouching to the left, tail curled into a spiral"></div>

    <p class="label__of">di</p>

    <p class="label__brand">Río Ámbar</p>

    <div class="label__details">
      <span class="label__batch"><em>Raccolta No.</em> 01</span>
      <span class="label__abv">41.0 <em>Vol</em></span>
    </div>

    <div class="label__rule"></div>
    <div class="label__ornament" role="img" aria-label="Olive green geometric ornamental pattern band"></div>
  </main>
</body>
</html>
```